Meridale Real Estate

We are looking for help with web design for a new company that is revolutionizing the real estate world on the listing side: by charing per hour for top level professional real estate services. We would like the concept to be simple, clean and easily understood.
Updates

We want this website to actually function, not just a static design.

Industry/Entity Type

Real Estate

```html
<!DOCTYPE html>
<html lang="en">
<head>
<meta charset="utf-8">
<title>Meridale Real Estate – Find a Place to Stay</title>
<link rel="stylesheet" href="https://fonts.googleapis.com/css2?family=Marcellus&family=Roboto+Condensed:wght@400;700&family=Open+Sans:wght@400;700&display=swap">
<style>
  :root {
    --ink-dark: #111214;
    --bar-dark: #161719;
    --sky: #86c8e5;
    --sky-deep: #6fb8da;
    --paper: #f5f5f5;
    --card-cap: #2b2b2b;
    --text-grey: #444;
    --white: #ffffff;
    --accent-red: #f2604f;
    --select-blue: #7cc4e4;
    --help-top: #5a5a5a;
    --help-bottom: #3a3a3a;
  }
  * { box-sizing: border-box; margin: 0; padding: 0; }
  html, body { width: 796px; height: 1200px; overflow: hidden; }
  body {
    position: relative;
    background: var(--ink-dark);
    font-family: "Roboto Condensed", "Arial Narrow", sans-serif;
    color: var(--white);
  }
  a { color: inherit; text-decoration: none; }

  /* ---------- top utility bar ---------- */
  .utility-bar {
    position: absolute; left: 0; top: 0; width: 796px; height: 23px;
    background: var(--ink-dark);
    display: flex; align-items: center; justify-content: flex-end;
    padding-right: 116px; font-family: "Open Sans", sans-serif; font-size: 8px;
  }
  .utility-bar .sign-in { padding-right: 9px; border-right: 1px solid #c0392b; margin-right: 9px; line-height: 12px; }
  .utility-bar .follow { margin-right: 6px; }
  .social-dot { width: 17px; height: 17px; border: 1px solid var(--white); border-radius: 50%; margin-left: 3px; }

  /* ---------- hero ---------- */
  .hero {
    position: absolute; left: 0; top: 23px; width: 796px; height: 368px;
    background:
      radial-gradient(ellipse at 78% 45%, rgba(120,110,130,0.55), rgba(0,0,0,0) 40%),
      linear-gradient(180deg, #c9cbcf 0%, #a7a9ad 35%, #7c7e83 65%, #55575c 100%);
  }
  .hero-photo { position: absolute; inset: 0; }
  .brand {
    position: absolute; left: 104px; top: 52px;
    display: flex; align-items: center; gap: 7px;
    font-family: "Roboto Condensed", sans-serif; font-weight: 700; font-size: 15px;
    letter-spacing: 0.5px; color: var(--white); white-space: nowrap;
  }
  .brand-dot { width: 12px; height: 12px; border-radius: 50%; background: var(--white); }
  .main-nav { position: absolute; top: 0; left: 400px; display: flex; height: 49px; font-family: "Open Sans", sans-serif; font-size: 9px; }
  .main-nav a { display: flex; align-items: center; justify-content: center; color: var(--ink-dark); }
  .main-nav a.active { background: var(--sky); color: var(--white); width: 45px; }
  .main-nav a:nth-child(2) { width: 88px; padding-left: 8px; }
  .main-nav a:nth-child(3) { width: 72px; }
  .main-nav a:nth-child(4) { width: 68px; }

  .hero-title {
    position: absolute; left: 97px; top: 168px;
    font-family: "Marcellus", serif; font-size: 36px; letter-spacing: 1px; font-weight: 400;
    color: var(--ink-dark);
  }
  .hero-sub {
    position: absolute; left: 99px; top: 216px; width: 408px; height: 21px;
    background: var(--ink-dark); padding-left: 5px;
    font-size: 17px; line-height: 21px;
  }
  .search-head {
    position: absolute; left: 97px; top: 277px; width: 599px; height: 27px;
    background: rgba(230,230,232,0.85); color: var(--ink-dark);
    font-size: 17px; line-height: 27px; padding-left: 16px;
  }
  .search-bar {
    position: absolute; left: 97px; top: 304px; width: 599px; height: 53px;
    background: rgba(60,75,85,0.55);
  }
  .select {
    position: absolute; top: 12px; height: 26px; background: var(--select-blue);
    font-size: 11px; line-height: 26px; padding-left: 7px; color: #e8f5fb;
  }
  .select::after {
    content: ""; position: absolute; right: 0; top: 0; width: 22px; height: 26px;
    border-left: 1px solid rgba(255,255,255,0.8);
  }
  .select svg { position: absolute; right: 7px; top: 11px; z-index: 1; }
  .select.accommodation { left: 26px; width: 154px; }
  .select.location { left: 190px; width: 126px; }
  .select.price { left: 326px; width: 126px; }
  .select-btn {
    position: absolute; left: 464px; top: 14px; width: 71px; height: 23px;
    background: var(--accent-red); font-size: 13px; line-height: 23px; text-align: center; letter-spacing: 0.5px;
  }

  /* ---------- welcome ---------- */
  .welcome { position: absolute; left: 0; top: 391px; width: 796px; height: 160px; background: var(--sky); }
  .welcome h2 {
    position: absolute; left: 113px; top: 22px;
    font-family: "Marcellus", serif; font-weight: 400; font-size: 27px; letter-spacing: 0.5px;
  }
  .welcome p {
    position: absolute; left: 113px; top: 63px; width: 566px;
    font-family: "Open Sans", sans-serif; font-size: 7.3px; line-height: 14.5px; text-align: justify;
  }

  /* ---------- what we are ---------- */
  .about { position: absolute; left: 0; top: 551px; width: 796px; height: 316px; background: var(--paper); }
  .about h2 {
    position: absolute; left: 113px; top: 26px; color: var(--ink-dark);
    font-family: "Marcellus", serif; font-weight: 400; font-size: 28px; letter-spacing: 1px;
  }
  .service-card { position: absolute; top: 78px; width: 175px; text-align: center; }
  .service-card:nth-of-type(1) { left: 115px; }
  .service-card:nth-of-type(2) { left: 308px; }
  .service-card:nth-of-type(3) { left: 500px; }
  .service-photo { position: relative; height: 128px; }
  .service-photo .caption {
    position: absolute; left: 0; bottom: 0; width: 100%; height: 25px;
    background: var(--card-cap); font-size: 13px; line-height: 25px;
  }
  .service-card p {
    margin: 11px auto 0; width: 168px; color: var(--text-grey);
    font-family: "Open Sans", sans-serif; font-size: 7.3px; line-height: 13px;
  }
  .btn {
    display: inline-block; background: var(--sky); color: var(--ink-dark);
    font-size: 12px; height: 20px; line-height: 20px; padding: 0 9px;
  }
  .service-card .btn { margin-top: 13px; width: 67px; padding: 0; }

  /* ---------- help ---------- */
  .help {
    position: absolute; left: 0; top: 867px; width: 796px; height: 253px;
    background: linear-gradient(180deg, var(--help-top), var(--help-bottom));
  }
  .help-photo { position: absolute; left: 60px; top: 10px; width: 280px; height: 243px; }
  .help h2 {
    position: absolute; left: 369px; top: 24px;
    font-family: "Marcellus", serif; font-weight: 400; font-size: 25px; line-height: 27px; letter-spacing: 0.5px;
  }
  .help p {
    position: absolute; left: 375px; top: 88px; width: 300px;
    font-size: 11px; line-height: 16.4px; color: #eee; text-align: justify;
  }
  .help .btn { position: absolute; left: 375px; top: 198px; font-size: 12px; padding: 0 8px; }

  /* ---------- footer ---------- */
  .footer-nav {
    position: absolute; left: 0; top: 1120px; width: 796px; height: 27px; background: #0d0e10;
    font-family: "Open Sans", sans-serif; font-size: 8px;
  }
  .footer-nav a { position: absolute; top: 0; height: 27px; line-height: 27px; }
  .footer-nav a.active { left: 269px; width: 42px; text-align: center; background: var(--sky); }
  .footer-nav a:nth-child(2) { left: 327px; }
  .footer-nav a:nth-child(3) { left: 415px; }
  .footer-nav a:nth-child(4) { left: 479px; }
  .footer { position: absolute; left: 0; top: 1147px; width: 796px; height: 53px; background: var(--bar-dark); }
  .footer .social { position: absolute; left: 364px; top: 8px; display: flex; gap: 5px; }
  .footer .social span { width: 18px; height: 18px; background: #4d6fa9; border-radius: 2px; }
  .footer .social span:nth-child(2) { background: var(--sky-deep); }
  .footer .social span:nth-child(3) { background: #c8463a; }
  .copyright {
    position: absolute; left: 0; top: 31px; width: 796px; text-align: center; padding-right: 6px;
    font-family: "Open Sans", sans-serif; font-weight: 700; font-size: 10px; color: #9a9a9a;
  }
</style>
</head>
<body>

<header class="utility-bar">
  <a class="sign-in" href="#">Sign in</a>
  <span class="follow">Follow Us:</span>
  <span class="social-dot" aria-label="Social profile"></span>
  <span class="social-dot" aria-label="Social profile"></span>
  <span class="social-dot" aria-label="Social profile"></span>
</header>

<section class="hero">
  <div class="hero-photo" role="img" aria-label="City skyline seen from a rooftop with a traveller in motion blur"></div>
  <a class="brand" href="#"><span class="brand-dot"></span>Meridale Real Estate</a>
  <nav class="main-nav">
    <a class="active" href="#">Home</a>
    <a href="#">What we offer</a>
    <a href="#">Location</a>
    <a href="#">Contact us</a>
  </nav>
  <h1 class="hero-title">FIND A PLACE TO STAY</h1>
  <div class="hero-sub">Rent from people in over 34,000 cities and 192 countries.</div>
  <div class="search-head">Find your perfect place</div>
  <form class="search-bar">
    <div class="select accommodation">Select a Accomodation
      <svg width="8" height="5" viewBox="0 0 8 5"><path d="M0 0h8L4 5z" fill="#fff"/></svg></div>
    <div class="select location">Select a Location
      <svg width="8" height="5" viewBox="0 0 8 5"><path d="M0 0h8L4 5z" fill="#fff"/></svg></div>
    <div class="select price">Price Range
      <svg width="8" height="5" viewBox="0 0 8 5"><path d="M0 0h8L4 5z" fill="#fff"/></svg></div>
    <div class="select-btn">SELECT</div>
  </form>
</section>

<section class="welcome">
  <h2>WELCOME TO HOME RENT</h2>
  <p>Sed ut perspiciatis unde omnis iste natus error sit voluptatem accusantium doloremque laudantium, totam rem aperiam, eaque ipsa quae ab illo inventore veritatis et quasi architecto beatae vitae dicta sunt explicabo. Nemo enim ipsam voluptatem quia voluptas sit aspernatur aut odit aut fugit, sed quia consequuntur magni dolores eos qui ratione voluptatem sequi nesciunt. Neque porro quisquam est, qui dolorem ipsum quia dolor sit amet, consectetur, adipisci velit, sed quia non numquam eius modi tempora incidunt ut labore et dolore magnam aliquam quaerat voluptatem. Ut enim ad minima veniam, quis nostrum exercitationem ullam corporis suscipit laboriosam, nisi ut aliquid ex ea commodi consequatur.</p>
</section>

<section class="about">
  <h2>WHAT WE ARE</h2>
  <article class="service-card">
    <div class="service-photo" role="img" aria-label="Hand touching a tablet with floating digital icons" style="background:linear-gradient(160deg,#bfe0f2,#4f8fc0 60%,#2c5d8c)">
      <div class="caption">Lorem ipsum dolor</div>
    </div>
    <p>Sed ut perspiciatis unde omnis iste natus error sit voluptatem accusantium doloremque.</p>
    <a class="btn" href="#">Click Here</a>
  </article>
  <article class="service-card">
    <div class="service-photo" role="img" aria-label="Modern villa with a lit pool at dusk" style="background:linear-gradient(180deg,#2d3d5c 0%,#8a6a45 55%,#d8a35a 70%,#3aa7c9 90%)">
      <div class="caption">Lorem ipsum dolor</div>
    </div>
    <p>Sed ut perspiciatis unde omnis iste natus error sit voluptatem accusantium doloremque.</p>
    <a class="btn" href="#">Click Here</a>
  </article>
  <article class="service-card">
    <div class="service-photo" role="img" aria-label="Agent handing over house keys in front of a home" style="background:linear-gradient(120deg,#d9c4a2 0%,#b08a66 45%,#1f5fa8 75%,#2f74c0)">
      <div class="caption">Lorem ipsum dolor</div>
    </div>
    <p>Sed ut perspiciatis unde omnis iste natus error sit voluptatem accusantium doloremque.</p>
    <a class="btn" href="#">Click Here</a>
  </article>
</section>

<section class="help">
  <div class="help-photo" role="img" aria-label="Motion-blurred figure of a person in a light shirt" style="background:radial-gradient(ellipse at 50% 60%,rgba(225,225,228,0.4),rgba(90,90,90,0) 70%)"></div>
  <h2>WE ARE ALWAYS READY<br>TO HELP YOU.</h2>
  <p>Sed ut perspiciatis unde omnis iste natus error sit voluptatem accusantium doloremque laudantium, totam rem aperiam, eaque ipsa quae ab illo inventore veritatis et quasi architecto beatae vitae dicta sunt explicabo. Nemo enim ipsam voluptatem quia voluptas sit aspernatur aut odit aut fugit, sed quia consequuntur magni dolores eos qui ratione voluptatem sequi.</p>
  <a class="btn" href="#">Click More</a>
</section>

<nav class="footer-nav">
  <a class="active" href="#">Home</a>
  <a href="#">What we offer</a>
  <a href="#">Location</a>
  <a href="#">Contact us</a>
</nav>

<footer class="footer">
  <div class="social"><span></span><span></span><span></span></div>
  <p class="copyright">© Copyrights 2015 Meridale Real Estate. All Right Reserved</p>
</footer>

</body>
</html>
```